Building company buisness cards

We are looking for a sharp modern new look for our business cards.
We are a New Zealand based company that specialises in house and land packages.
We have attached a photo of the current logo and would like to see if it can be improved somehow if needed.
We are open to any colours but we have chosen green at this stage.
Feel free to change the font and make the logo smarter looking.
Play with the colours and see what looks best.

We want a card that looks so good know one will want to throw it away!

Target Market(s)

Home buyers

Industry/Entity Type

Building

Contact Information for Business Card

Derek Tolvane
0217394062
dtolvane@quillmarkhomesteads.co.nz
quillmarkhomesteads.co.nz

Font styles to use
Serif
Sans Serif

Colors

Designer to choose colors to be used in the design.

Requirements
Must have
• Logo and company name on one side, details on the other side
Nice to have
• Color codes for the original green are HEX #4a8028, RGB(74,128,40), CMYK(42,0,69,50)
• Round corners, Raised and/or spot UV

```html
<!DOCTYPE html>
<html lang="en">
<head>
<meta charset="utf-8">
<title>Quillmark Homesteads – Business Card</title>
<link rel="stylesheet" href="https://fonts.googleapis.com/css2?family=Lato:wght@700;900&family=Open+Sans:wght@400&display=swap">
<style>
  :root {
    --brand-green: #4a8028;
    --paper: #ffffff;
    --backdrop: #2b2b2b;
    --rule-grey: #d9d9d9;
  }
  * { box-sizing: border-box; margin: 0; padding: 0; }
  html, body { width: 1200px; height: 1200px; overflow: hidden; }
  body { background: var(--backdrop); position: relative; font-family: "Lato", sans-serif; }

  .card {
    position: absolute;
    top: 310px;
    width: 364px;
    height: 593px;
    overflow: hidden;
  }
  .card--front { left: 234px; background: var(--paper); }
  .card--back { left: 627px; width: 369px; background: var(--brand-green); }

  .wordmark {
    position: absolute;
    left: 0; right: 0;
    text-align: center;
    font-family: "Lato", sans-serif;
    font-weight: 900;
    color: var(--brand-green);
    line-height: 1;
  }
  .wordmark--front { top: 138px; }
  .wordmark__top { display: block; font-size: 28px; letter-spacing: 0.2px; }
  .wordmark__bottom { display: block; font-size: 37px; margin-top: 4px; letter-spacing: 0.2px; }

  .title-rule {
    position: absolute;
    top: 216px; left: 152px;
    width: 62px; height: 1px;
    background: var(--rule-grey);
  }

  .roof-band { position: absolute; left: 0; top: 0; width: 364px; height: 593px; }

  .holder-name {
    position: absolute;
    top: 397px; left: 0; right: 0;
    text-align: center;
    font-family: "Lato", sans-serif;
    font-weight: 700;
    font-size: 20px;
    color: var(--paper);
    text-transform: uppercase;
  }

  .contact-icons {
    position: absolute;
    top: 450px; left: 0; right: 0;
    display: flex; justify-content: center; align-items: center; gap: 6px;
  }
  .contact-icons__rule { width: 40px; height: 1px; background: var(--paper); }
  .contact-icons__rule:first-child { margin-right: 2px; }
  .contact-icons__rule:last-child { margin-left: 2px; }
  .contact-icon {
    width: 22px; height: 22px; border-radius: 5px;
    background: var(--paper);
    display: flex; align-items: center; justify-content: center;
  }
  .contact-icon svg { width: 14px; height: 14px; }

  .contact-details {
    position: absolute;
    top: 484px; left: 0; right: 0;
    text-align: center;
    font-family: "Open Sans", sans-serif;
    font-size: 16.5px;
    line-height: 21px;
    color: var(--paper);
  }

  .wordmark--back { top: 270px; color: var(--paper); }
  .wordmark--back .wordmark__top { font-size: 40px; }
  .wordmark--back .wordmark__bottom { font-size: 50px; margin-top: 6px; }
</style>
</head>
<body>

<section class="card card--front" aria-label="Business card front">
  <h1 class="wordmark wordmark--front">
    <span class="wordmark__top">quillmark</span>
    <span class="wordmark__bottom">homesteads.</span>
  </h1>
  <div class="title-rule"></div>

  <svg class="roof-band" viewBox="0 0 364 593" aria-hidden="true">
    <path d="M0 355 L172 244 Q182 237 192 244 L364 355 L364 593 L0 593 Z" fill="var(--brand-green)"/>
    <polyline points="0,378 182,265 364,380" fill="none" stroke="var(--paper)" stroke-width="3.5" stroke-linejoin="round"/>
  </svg>

  <p class="holder-name">Derek Tolvane</p>

  <div class="contact-icons">
    <span class="contact-icons__rule"></span>
    <span class="contact-icon" aria-label="Phone">
      <svg viewBox="0 0 16 16"><path d="M4 1.5l2.2 3-1.3 1.6c.8 1.9 2.3 3.4 4.2 4.2l1.6-1.3 3 2.2-1 2.6C8 13.6 2.4 8 2.2 2.5z" fill="var(--brand-green)"/></svg>
    </span>
    <span class="contact-icon" aria-label="Email">
      <svg viewBox="0 0 16 16"><rect x="1.5" y="3.5" width="13" height="9" fill="var(--brand-green)"/><polyline points="1.5,3.5 8,9 14.5,3.5" fill="none" stroke="var(--paper)" stroke-width="1.2"/></svg>
    </span>
    <span class="contact-icon" aria-label="Website">
      <svg viewBox="0 0 16 16"><circle cx="8" cy="8" r="6.5" fill="var(--brand-green)"/><ellipse cx="8" cy="8" rx="2.6" ry="6.5" fill="none" stroke="var(--paper)" stroke-width="1"/><line x1="1.5" y1="8" x2="14.5" y2="8" stroke="var(--paper)" stroke-width="1"/></svg>
    </span>
    <span class="contact-icons__rule"></span>
  </div>

  <address class="contact-details" style="font-style: normal;">
    0217394062<br>
    dtolvane@quillmarkhomesteads.co.nz<br>
    www.quillmarkhomesteads.co.nz
  </address>
</section>

<section class="card card--back" aria-label="Business card back">
  <p class="wordmark wordmark--back">
    <span class="wordmark__top">quillmark</span>
    <span class="wordmark__bottom">homesteads.</span>
  </p>
</section>

</body>
</html>
```